The Vantor Codex Book Cover

"The Vantor Codex" is a book I wrote with the slogan "Unlock Performance, Spark Engagement: Master the Art of Building Winning Cultures in Today's Hybrid World". The book is designed around a methodology that's mine and that I attached. I would love to see the graphic of the methodology integrated in the design in a very subtle way. Use colors from the model but the book cover should be catchy, modern and engaging to the eye.
Overall the book is about three key elements towards success:
- (Self) Directions (purpose)
- Human experience (people and psychological safety)
- Maximize engagement
The methodology is a FLOW so flow is something that could be incorporated as well in the concept.
Low design quality
Managers and Teams

```html
<!DOCTYPE html>
<html lang="en">
<head>
<meta charset="UTF-8">
<title>The Vantor Codex – Book Cover</title>
<link rel="stylesheet" href="https://fonts.googleapis.com/css2?family=Playfair+Display:wght@700;800&family=Oswald:wght@500;600&family=Montserrat:wght@400;500;700&display=swap">
<style>
  :root {
    --stage: #c9d9e1;
    --cover-light: #2f7f8f;
    --cover-dark: #184e60;
    --title-white: #f4f6f5;
    --title-aqua: #5fd6ca;
    --subtitle: #e3f2ef;
    --tagline: #d5e8e8;
    --rule: #cfe3e3;
    --author-light: #c9dcdd;
    --author-strong: #ffffff;
  }
  * { box-sizing: border-box; margin: 0; padding: 0; }
  html, body {
    width: 1200px;
    height: 1182px;
    overflow: hidden;
    background: var(--stage);
  }
  .canvas {
    position: relative;
    width: 1200px;
    height: 1182px;
  }
  .cover {
    position: absolute;
    left: 230px;
    top: 51px;
    width: 740px;
    height: 1080px;
    background: radial-gradient(ellipse at 35% 25%, var(--cover-light) 0%, #256c7d 45%, var(--cover-dark) 100%);
    overflow: hidden;
  }
  .taglines {
    position: absolute;
    left: 60px;
    right: 60px;
    top: 196px;
    display: flex;
    justify-content: space-between;
    font-family: "Montserrat", sans-serif;
    font-weight: 700;
    font-size: 15px;
    letter-spacing: 4px;
    color: var(--tagline);
  }
  .tagline {
    padding: 6px 0;
    border-top: 2px solid var(--rule);
    border-bottom: 2px solid var(--rule);
  }
  .title {
    position: absolute;
    left: 0;
    right: 0;
    top: 170px;
    text-align: center;
    font-family: "Playfair Display", serif;
    font-weight: 800;
    line-height: 0.9;
  }
  .title-the {
    display: block;
    font-size: 84px;
    color: var(--title-white);
    margin-bottom: 8px;
  }
  .title-main {
    display: block;
    font-size: 150px;
    color: var(--title-white);
    letter-spacing: -2px;
  }
  .title-accent {
    display: block;
    font-size: 168px;
    color: var(--title-aqua);
    letter-spacing: -3px;
  }
  .subtitle {
    position: absolute;
    left: 0;
    right: 0;
    top: 560px;
    text-align: center;
    font-family: "Oswald", sans-serif;
    font-weight: 600;
    font-size: 27px;
    line-height: 1.2;
    color: var(--subtitle);
    text-transform: uppercase;
  }
  .flow-artwork {
    position: absolute;
    left: 130px;
    top: 650px;
    width: 520px;
    height: 300px;
    border-radius: 50%;
    background:
      radial-gradient(circle at 30% 55%, rgba(232,110,130,0.85) 0%, rgba(170,90,150,0.6) 30%, transparent 58%),
      radial-gradient(circle at 72% 45%, rgba(190,190,70,0.8) 0%, rgba(80,180,170,0.6) 32%, transparent 60%),
      radial-gradient(ellipse at 50% 50%, rgba(255,255,255,0.25) 0%, transparent 70%);
  }
  .author {
    position: absolute;
    left: 0;
    right: 0;
    top: 985px;
    text-align: center;
    font-family: "Montserrat", sans-serif;
    font-size: 38px;
    letter-spacing: 16px;
    text-transform: uppercase;
  }
  .author-first { font-weight: 400; color: var(--author-light); }
  .author-last { font-weight: 700; color: var(--author-strong); }
</style>
</head>
<body>
  <main class="canvas">
    <section class="cover">
      <div class="taglines">
        <span class="tagline">Unlock Performance</span>
        <span class="tagline">Spark Engagement</span>
      </div>
      <h1 class="title">
        <span class="title-the">The</span>
        <span class="title-main">Vantor</span>
        <span class="title-accent">Codex</span>
      </h1>
      <p class="subtitle">Master the art of building winning<br>cultures in today's hybrid world</p>
      <div class="flow-artwork" role="img" aria-label="Glowing flow illustration: a colourful segmented methodology wheel over a compass, merging into a circle with people figures and hands"></div>
      <p class="author"><span class="author-first">Lise</span> <span class="author-last">Marten</span></p>
    </section>
  </main>
</body>
</html>
```